New Business Card Design Project LORVANTI-Italy

we are LORVANTI-Italy
our company in the market for 3 years we are luxury cosmetic company and its about time for a facelift :)
i will like to have elegant luxurious and unique business card
that will give the person that get it a unique, luxurious and elegant impression
I'm VERY OPEN FOR NEW IDEAS , even duo i add a few files of things that i see on line and i like them

i add my logo as well
my website is LORVANTI.COM
(if you would like to see the main style that we have)

Target Market(s)

adult that have money :)

Industry/Entity Type

Business

Contact Information for Business Card

Name - Dario Lorvanti
Position - CEO and CO Founder
address - 4817 E Halvern
telephone - 555-384-1926
email - dario@lorvanti.com
fax - 555-384-1926
website - LORVANTI.COM

Colors
000000
959595
fbee3e
ffffff

Requirements
Must have
• big logo in GOLD color
• elegant look
• impressive
Nice to have
• not must but maybe classy pattern background
• not must but maybe emblem
• maybe clear plastic business card
Should not have
• colors
• images

```html
<!DOCTYPE html>
<html lang="en">
<head>
<meta charset="utf-8">
<title>LORVANTI Italy – Business Card</title>
<link href="https://fonts.googleapis.com/css2?family=Cinzel:wght@500&family=Libre+Baskerville:wght@700&family=Roboto:wght@300;400&display=swap" rel="stylesheet">
<style>
  :root{
    --backdrop:#2b2b2b;
    --card-dark-top:#3b352d;
    --card-dark-bottom:#1e1a16;
    --gold:#d9b24a;
    --gold-deep:#a87d2c;
    --cream-light:#fdf7e6;
    --cream:#f4e4ba;
    --ink-brown:#6b5636;
    --ink-grey:#4a4540;
    --rule:#b59a66;
  }
  *{margin:0;padding:0;box-sizing:border-box}
  html,body{width:1200px;height:900px;overflow:hidden}
  body{background:var(--backdrop);position:relative}

  .card{
    position:absolute;width:520px;height:298px;border-radius:26px;overflow:hidden;
    box-shadow:0 18px 40px rgba(0,0,0,.45);
  }

  /* front */
  .card--front{
    left:230px;top:95px;
    background:linear-gradient(160deg,var(--card-dark-top),var(--card-dark-bottom));
    display:flex;flex-direction:column;align-items:center;justify-content:center;
  }
  .brand-circle{
    width:84px;height:84px;border-radius:50%;border:3px solid var(--gold);margin-bottom:20px;
  }
  .brand-name{
    font-family:"Cinzel",serif;font-weight:500;font-size:44px;letter-spacing:2px;
    color:var(--gold);line-height:1;
  }
  .brand-rule{width:250px;height:2px;background:var(--gold);margin:10px 0 8px}
  .brand-country{
    font-family:"Cinzel",serif;font-weight:500;font-size:15px;letter-spacing:3px;color:var(--gold);
  }

  /* back */
  .card--back{
    left:450px;top:490px;
    background:linear-gradient(135deg,var(--cream-light) 0%,var(--cream) 100%);
  }
  .emblem-area{
    position:absolute;left:-80px;top:60px;width:330px;height:330px;border-radius:50%;
    background:radial-gradient(circle at 45% 45%,#f6dc93 0%,var(--gold) 45%,var(--gold-deep) 100%);
    opacity:.85;
  }
  .holder{
    position:absolute;right:34px;top:26px;text-align:right;
  }
  .holder-name{
    font-family:"Libre Baskerville",serif;font-weight:700;font-size:24px;color:var(--ink-brown);
  }
  .holder-title{
    font-family:"Roboto",sans-serif;font-weight:400;font-size:10px;color:var(--ink-grey);margin-top:3px;
  }
  .holder-rule{
    position:absolute;right:34px;top:88px;width:190px;height:1px;background:var(--rule);
  }
  .contact{
    position:absolute;right:34px;top:104px;list-style:none;
    font-family:"Roboto",sans-serif;font-weight:300;font-size:12px;color:var(--ink-grey);
  }
  .contact li{display:flex;justify-content:flex-end;align-items:center;gap:8px;line-height:1.35;margin-bottom:6px}
  .contact .lines{text-align:right}
  .contact svg{width:12px;height:12px;flex:none;fill:var(--ink-brown)}
</style>
</head>
<body>

<section class="card card--front" aria-label="Business card front">
  <span class="brand-circle" aria-hidden="true"></span>
  <span class="brand-name">LORVANTI</span>
  <span class="brand-rule" aria-hidden="true"></span>
  <span class="brand-country">ITALY</span>
</section>

<section class="card card--back" aria-label="Business card back">
  <div class="emblem-area" role="img" aria-label="Large gold brand emblem decoration"></div>

  <div class="holder">
    <p class="holder-name">Dario Lorvanti</p>
    <p class="holder-title">CEO and CO Founder</p>
  </div>
  <span class="holder-rule" aria-hidden="true"></span>

  <ul class="contact">
    <li>
      <span class="lines">4817 E Halvern<br>Harlow Nevada 89990</span>
      <svg viewBox="0 0 12 12" aria-hidden="true"><path d="M11 1 1 5.5l4.5 1.2L6.7 11z"/></svg>
    </li>
    <li>
      <span>555 384 1926</span>
      <svg viewBox="0 0 12 12" aria-hidden="true"><path d="M2.5 1 4.5 1 5.3 3.6 4 4.6c.7 1.5 1.9 2.7 3.4 3.4l1-1.3L11 7.5v2c0 .8-.7 1.5-1.5 1.5C5 11 1 7 1 2.5 1 1.7 1.7 1 2.5 1z"/></svg>
    </li>
    <li>
      <span>dario@lorvanti.com</span>
      <svg viewBox="0 0 12 12" aria-hidden="true"><path d="M1 2.5h10v7H1z M1.6 3 6 6.5 10.4 3" fill="none" stroke="currentColor"/><path d="M1 2.5h10L6 6.3z"/><path d="M1 3.5v6h10v-6L6 7.2z"/></svg>
    </li>
    <li>
      <span>555 384 1926</span>
      <svg viewBox="0 0 12 12" aria-hidden="true"><path d="M3 1h5v3H3z M1.5 4.5h9v5h-9z M3.5 8h5v3h-5z"/></svg>
    </li>
    <li>
      <span>www.lorvanti.com</span>
      <svg viewBox="0 0 12 12" aria-hidden="true"><circle cx="6" cy="6" r="5"/><path d="M1 6h10M6 1c2 2.5 2 7.5 0 10M6 1c-2 2.5-2 7.5 0 10" stroke="#f4e4ba" stroke-width=".8" fill="none"/></svg>
    </li>
  </ul>
</section>

</body>
</html>
```